Coastal Learner Bureau business cards

Australian company about to start offering its services. We recruit international students to come to study English, vocational education and postgraduate courses in Australia. We help them find the institution and select the right city they want to come to Australia. We are a young, online oriented and supportive agency. Our clients are between 18 and 35 years old, mainly University students, young professionals or people with work experience. We provide much more information that any other agency offer. We administrate a Facebook group with more than 11.000 members that daily ask questions about general information when coming to Australia, while they are here and even after they leave the country

Target Market(s)

International students from South America, Central America and Europe

Industry/Entity Type

Student

Contact Information for Business Card

Tomas Bilbrea
Managing Director
tomas@kelvarin.com.au
www.kelvoria.com.au
+61 491058264
Melbourne, Australia

Font styles to use
Serif
Sans Serif

Colors

Designer to choose colors to be used in the design.

Requirements
Must have
• Horizontal design
• Standard business card size and shape. If font uses green or yellow colours, they will have to match the ones from the logo
Nice to have
• UPDATE: Use the contents of the green image to design one of the card sides. Use our logo in the background of that side as watermark.
• Passport image, or immigration stamps. A picture of the Yarra River (from Melbourne) would be cool as well.
Should not have
• Non-standard business card size and shape
• Not black as the background colour of any sides as we are not a VIP agency or a hight class service. We are orientes to young people and they like colours, pictures, something attractive.
• Vertical design
• NO YELLOW or BLACK AS THE BACKGROUND COLOUR OF ANY SIDE OF THE BIZ CARD

```html
<!DOCTYPE html>
<html lang="en">
<head>
<meta charset="utf-8">
<title>Kelvoria Business Cards</title>
<link rel="stylesheet" href="https://fonts.googleapis.com/css2?family=Jost:wght@400;500;600&display=swap">
<style>
  :root {
    --brand-green: #11633f;
    --brand-yellow: #e6bb2a;
    --ink: #333333;
    --paper: #ffffff;
    --backdrop: #e9ebea;
  }
  * { box-sizing: border-box; margin: 0; padding: 0; }
  html, body { width: 1200px; height: 900px; overflow: hidden; }
  body {
    background: var(--backdrop);
    font-family: "Jost", Arial, sans-serif;
    position: relative;
  }
  .card {
    position: absolute;
    left: 280px;
    width: 640px;
    height: 366px;
    background: var(--paper);
    box-shadow: 0 6px 18px rgba(0,0,0,0.18);
    overflow: hidden;
  }
  .card--front { top: 60px; }
  .card--back { top: 474px; }

  .brand-name {
    font-weight: 600;
    color: var(--brand-green);
    letter-spacing: 0.5px;
    display: flex;
    align-items: center;
    gap: 10px;
  }
  .brand-dot {
    width: 14px; height: 14px;
    border-radius: 50%;
    background: var(--brand-yellow);
  }
  .card--front .brand-name {
    position: absolute;
    top: 130px; left: 0; right: 0;
    justify-content: center;
    font-size: 52px;
  }
  .tagline {
    position: absolute;
    bottom: 40px; left: 0; right: 0;
    text-align: center;
    font-size: 14px;
    letter-spacing: 1px;
    color: var(--ink);
  }

  .card--back .brand-name {
    position: absolute;
    top: 140px; left: 40px;
    font-size: 40px;
  }
  .divider {
    position: absolute;
    left: 290px; top: 120px;
    width: 2px; height: 150px;
    background: var(--brand-green);
  }
  .contact-block {
    position: absolute;
    left: 315px; top: 118px;
  }
  .person-name {
    font-size: 27px;
    font-weight: 600;
    letter-spacing: 1.5px;
    color: var(--brand-green);
    text-transform: uppercase;
    line-height: 1.1;
  }
  .person-role {
    font-size: 18px;
    color: var(--ink);
    margin-bottom: 12px;
    letter-spacing: 0.5px;
  }
  .contact-list { list-style: none; }
  .contact-list li {
    display: flex;
    align-items: center;
    gap: 12px;
    font-size: 15.5px;
    letter-spacing: 1px;
    color: var(--ink);
    line-height: 1.6;
  }
  .contact-list svg { width: 14px; height: 14px; flex: none; fill: var(--brand-green); }
  .bottom-wave {
    position: absolute;
    left: 0; bottom: 0;
    width: 640px; height: 366px;
  }
</style>
</head>
<body>

<section class="card card--front">
  <div class="brand-name"><span class="brand-dot"></span>Kelvoria</div>
  <p class="tagline">Hacemos más por ti!</p>
</section>

<section class="card card--back">
  <svg class="bottom-wave" viewBox="0 0 640 366" preserveAspectRatio="none" aria-hidden="true">
    <path d="M240 336 C420 334 560 330 640 320 L640 366 L240 366 Z" fill="var(--brand-yellow)"/>
    <path d="M0 298 C220 300 440 330 640 366 L0 366 Z" fill="var(--brand-green)" stroke="#ffffff" stroke-width="3"/>
  </svg>

  <div class="brand-name"><span class="brand-dot"></span>Kelvoria</div>
  <div class="divider"></div>

  <div class="contact-block">
    <h1 class="person-name">Tomas Bilbrea</h1>
    <p class="person-role">Managing Director</p>
    <ul class="contact-list">
      <li>
        <svg viewBox="0 0 14 14"><path d="M4 0.5h6a1 1 0 0 1 1 1v11a1 1 0 0 1-1 1H4a1 1 0 0 1-1-1v-11a1 1 0 0 1 1-1zm0.6 1.4v9h4.8v-9z"/></svg>
        +61 491058264
      </li>
      <li>
        <svg viewBox="0 0 14 14"><path d="M1 3h12v1L7 8 1 4z"/><path d="M1 5.3l6 4 6-4V11H1z"/></svg>
        tomas@kelvarin.com.au
      </li>
      <li>
        <svg viewBox="0 0 14 14"><path d="M6 1a5 5 0 0 1 4 8l3 3-1.2 1.2-3-3A5 5 0 1 1 6 1zm0 1.8a3.2 3.2 0 1 0 0 6.4 3.2 3.2 0 0 0 0-6.4z"/></svg>
        www.kelvoria.com.au
      </li>
      <li>
        <svg viewBox="0 0 14 14"><path d="M7 0.5a4.5 4.5 0 0 1 4.5 4.5C11.5 8.5 7 13.5 7 13.5S2.5 8.5 2.5 5A4.5 4.5 0 0 1 7 0.5zm0 2.8a1.7 1.7 0 1 0 0 3.4 1.7 1.7 0 0 0 0-3.4z"/></svg>
        Melbourne, Australia
      </li>
    </ul>
  </div>
</section>

</body>
</html>
```